Patent Law

Need to develop a home page for a patent lawyer.

Colors should go with logo, blues...

Company Name- Velun Tresk, PLLC

Company Overview-

I am an Intellectual Property Lawyer and focus on patents, copyrights, trademarks, & trade secrets. I work with small businesses and start ups in the chemical and biotech industries.

Why Us-

I am small firm that can provide large-firm service at a reasonable price. I also can charge flat-fees for entreprenuers in certain practice areas.

Services-
Intellectual Property
Patents
Copyrights
Trademarks
Trade secrets
Healthcare Compliance
Elder law
Wills
Trusts

Website we like-
http://www.quorvantlegal.example/ - within industry!!
http://www.daltrowemiko.example/
http://ulbrixtane.example/
http://thegravelcounsel.example/

Target Market(s)

My customers will be small business, specifically small start-up companies in the chemical and biotech arena.

Industry/Entity Type

Trade

Requirements
Must have
• Colors should go with logo, blues...

```html
<!DOCTYPE html>
<html lang="en">
<head>
<meta charset="utf-8">
<title>Velun Tresk, PLLC – Patent Law</title>
<link href="https://fonts.googleapis.com/css2?family=Alegreya+Sans:wght@400;500&display=swap" rel="stylesheet">
<style>
:root{
  --ink:#2b2b2b;
  --muted:#555;
  --rule:#c9c9c9;
  --brand:#1b5e9e;
  --brand-deep:#0f4a86;
  --accent-sky:#2e9be0;
  --footer:#0c66b0;
  --footer-base:#0a559a;
  --panel:#f3f3f3;
  --slab:#262626;
  --alert:#c0282b;
  --white:#fff;
}
*{box-sizing:border-box;margin:0;padding:0}
html,body{width:1106px;height:1200px;overflow:hidden}
body{position:relative;background:var(--white);font-family:"Alegreya Sans",sans-serif;color:var(--ink)}
.abs{position:absolute}
.top-rule{left:0;top:0;width:1106px;height:4px;background:var(--slab)}
.utility{left:93px;top:14px;width:921px;font-size:14.5px;color:var(--ink)}
.utility .phone{position:absolute;left:730px;top:1px;font-size:13.5px;display:flex;align-items:center;gap:8px}
.utility .sitemap{position:absolute;left:857px;top:0;font-size:14.5px}
.utility-line{left:93px;top:45px;width:921px;height:1px;background:var(--rule)}
.brand{left:93px;top:76px;display:flex;align-items:center;gap:8px;font-size:15px;letter-spacing:.5px;color:var(--ink);text-transform:uppercase}
.brand .mark{width:14px;height:14px;background:var(--brand)}
.nav{left:506px;top:46px;height:92px;display:flex}
.nav a{display:block;height:92px;padding:56px 14px 0;font-size:16px;color:var(--ink);text-decoration:none}
.nav a.active{background:var(--panel);border-top:4px solid var(--brand-deep);padding-top:52px}
.hero{left:0;top:138px;width:1106px;height:415px;background:linear-gradient(90deg,#e9e9e9 0%,#f4f4f4 45%,#ececec 100%)}
.hero-photo{left:544px;top:170px;width:424px;height:383px;background:linear-gradient(180deg,rgba(226,232,238,0) 0%,#dfe7ef 35%,#c7dbef 100%)}
.slab{left:115px;height:46px;background:var(--slab);font-size:26px;line-height:46px;padding:0 15px;white-space:nowrap}
.slab.one{top:231px;width:150px;color:#bdbdbd}
.slab.two{top:277px;width:301px;color:var(--white)}
.slab.three{top:323px;width:210px;color:var(--accent-sky)}
.hero-text{left:115px;top:384px;width:266px;font-size:14px;line-height:20.5px;color:#3a3a3a}
.hero-text b{font-weight:400;color:#111}
.dots{left:121px;top:532px;display:flex;gap:5px}
.dots span{width:13px;height:13px;border-radius:50%;background:#3e3e3e}
.dots span.on{background:var(--brand-deep)}
.section-title{top:586px;font-size:19px;font-weight:400;color:var(--brand-deep)}
.card{top:622px;height:254px;border:1px solid var(--rule);background:var(--white)}
.card .media{position:absolute;left:15px;top:11px;right:15px;height:120px}
.card .body{position:absolute;left:16px;top:139px;right:20px;font-size:14px;line-height:22px;color:#333}
.card a{color:var(--brand);text-decoration:none}
.services{display:grid;grid-template-columns:130px 1fr;line-height:23.5px}
.contact-lines p{margin-bottom:7.5px}
.footer{left:0;top:899px;width:1106px;height:264px;background:var(--footer);color:var(--white)}
.footer h3{position:absolute;top:38px;font-weight:400;font-size:29px}
.footer ul{position:absolute;top:89px;list-style:none;font-size:12.5px;line-height:20.3px}
.footer .qc-note{position:absolute;left:151px;top:88px;width:158px;font-size:12.5px;line-height:15px}
.field{position:absolute;left:152px;width:175px;height:21px;background:var(--white);border:1px solid #d7d7d7;font-size:8.5px;color:#666;padding:4px 8px}
.submit{position:absolute;left:152px;top:193px;width:52px;height:18px;background:var(--alert);font-size:8.5px;color:var(--white);text-align:center;line-height:18px}
.addr{position:absolute;left:796px;top:86px;font-size:12px;line-height:17px}
.addr dt{font-size:13.5px;letter-spacing:.3px}
.addr dd{margin-bottom:17px}
.base{left:0;top:1163px;width:1106px;height:37px;background:var(--footer-base)}
.social{position:absolute;left:158px;top:15px;display:flex;gap:11px}
.social span{width:9px;height:9px;border-radius:50%;background:var(--white)}
</style>
</head>
<body>
<div class="abs top-rule"></div>

<header>
  <div class="abs utility">Enquire with us about an assessment today!
    <span class="phone"><svg width="16" height="16" viewBox="0 0 16 16" aria-hidden="true"><path d="M3 1.5l3 3-1.6 1.8c.8 1.9 2.4 3.5 4.3 4.3L10.5 9l3 3-2 2.3C6 14 2 10 1.5 3.5z" fill="#e4412d"/></svg>1300 555 017</span>
    <span class="sitemap">SiteMap</span>
  </div>
  <div class="abs utility-line"></div>
  <div class="abs brand"><span class="mark"></span>Velun Tresk, PLLC</div>
  <nav class="abs nav">
    <a class="active" href="#">Home</a><a href="#">Firm</a><a href="#">People</a><a href="#">Practices</a><a href="#">Library</a><a href="#">News</a><a href="#">Contact</a>
  </nav>
</header>

<section class="abs hero"></section>
<div class="abs hero-photo" role="img" aria-label="Portrait photograph of a smiling attorney in a light blue shirt against a faint city skyline"></div>
<div class="abs slab one">Combining</div>
<div class="abs slab two">Industry Experience with</div>
<div class="abs slab three">Patent Expertise</div>
<p class="abs hero-text"><b>VELUN TRESK, PLLC</b> is full-service intelectual property firm with an emphasis on patent law and is the largest independant patent law firm in North Canada.</p>
<div class="abs dots"><span class="on"></span><span></span><span></span></div>

<h2 class="abs section-title" style="left:115px">About</h2>
<h2 class="abs section-title" style="left:420px">What we do</h2>
<h2 class="abs section-title" style="left:714px">Contact Us</h2>

<article class="abs card" style="left:114px;width:279px">
  <div class="media" role="img" aria-label="Team reviewing documents with a calculator at a desk" style="background:linear-gradient(135deg,#3a3a3a,#d9d9d9 45%,#f2f2f2 70%,#8fb7d6)"></div>
  <p class="body">VELUN TRESK, PLLC is nationally ranked intellectual property law firm combining patent law expertise with stable continuity of counsel to produce quality patent that stand up to scrunity. <a href="#">Read More</a></p>
</article>

<article class="abs card" style="left:414px;width:278px">
  <div class="media" role="img" aria-label="Group of colleagues gathered around a table" style="background:linear-gradient(135deg,#9aa4ad,#e8e8e8 40%,#6c7680 75%,#cfd6dc)"></div>
  <div class="body services" style="left:18px;right:8px;top:139px">
    <span>Intellectual Property</span><span>Health Compliance</span>
    <span>Patents</span><span>Elder Law</span>
    <span>Copyrights</span><span>Wills</span>
    <span>Trademarks</span><span>Trusts</span>
    <span>Trade Secrets</span><span></span>
  </div>
</article>

<article class="abs card" style="left:714px;width:279px">
  <div class="media" role="img" aria-label="Hands typing on a laptop keyboard" style="background:linear-gradient(135deg,#8fc0e6,#d6e8f6 45%,#e8d2c4 70%,#6c8fb0)"></div>
  <div class="body contact-lines" style="top:140px;right:10px">
    <p>Feel Free to Contact us for your any doubt :</p>
    <p>Telephone : 1300 555 017</p>
    <p>FAX : 1300 555 018</p>
    <p>Email : info@veluntresk.example</p>
  </div>
</article>

<footer class="abs footer">
  <h3 style="left:151px">Quick Contact</h3>
  <p class="qc-note">Submit and oue executives will call you.</p>
  <div class="field" style="top:128px">Name</div>
  <div class="field" style="top:161px">E mail</div>
  <div class="submit">Submit</div>

  <h3 style="left:392px">Quick Links</h3>
  <ul style="left:392px"><li>About</li><li>Firm</li><li>People</li><li>Practices</li><li>Library</li><li>News</li><li>Contact</li></ul>

  <h3 style="left:572px">Support Links</h3>
  <ul style="left:572px"><li>Privacy Policy</li><li>Copyright</li><li>Legal</li><li>Disclosure</li><li>Terms &amp; Conditions</li><li>Sitemap</li><li>Privacy</li></ul>

  <h3 style="left:796px">Contact Us</h3>
  <dl class="addr">
    <dt>ADDRESS :</dt><dd>214, Orrin Lane. East Hollow.<br>Marlowe, IN 40000, USA</dd>
    <dt>TELEPHONE :</dt><dd>+1 (555) 014-22-90</dd>
    <dt>E MAIL :</dt><dd>mail@veluntresk.example</dd>
  </dl>
</footer>

<div class="abs base">
  <div class="social"><span></span><span></span><span></span><span></span><span></span><span></span><span></span><span></span><span></span><span></span><span></span></div>
</div>
</body>
</html>
```